Business Card Design Project

This is to go hand in hand with our stationery project.
Target Market(s)
Business Professionals in the Finance, HR and C-Level management arena. They are global companies that run enterprise technology solutions/products.
Mostly Male, mid 30's to 60's.
Industry/Entity Type
Business
Font styles to use
Other font styles liked:
- Calibri
Colors
9bcb3c
000000
1b1b1b
c4c4c4
ffffff
Requirements
Must have
- Logo
Name, title, contact details, address on the front of the card.
ABN and web address need to be on the card, along with our tag line
See | Share | Do
We also require rounded corners and for the card to be landscape please.
Our green is
C98 M0 Y93 K0
Modern, contemporary and must have white space for people to write on.
Nice to have
- Consistent elements with the stationery design.
Should not have
- No 90's waves - We want the feeling of movement but no wavey lines.

```html
<!DOCTYPE html>
<html lang="en">
<head>
<meta charset="utf-8">
<title>Veltro Business Solutions – Business Cards</title>
<link rel="stylesheet" href="https://fonts.googleapis.com/css2?family=Open+Sans:wght@400;600;700&display=swap">
<style>
  :root {
    --green: #9bcb3c;
    --black: #000000;
    --ink: #1b1b1b;
    --grey: #c4c4c4;
    --white: #ffffff;
    --backdrop: #e4e6ea;
  }
  * { box-sizing: border-box; margin: 0; padding: 0; }
  html, body {
    width: 1200px; height: 960px; overflow: hidden;
    background: var(--backdrop);
    font-family: "Open Sans", Calibri, sans-serif;
    color: var(--ink);
  }
  .sheet {
    position: relative; width: 1200px; height: 960px;
  }
  .card {
    position: absolute; left: 240px;
    width: 720px; height: 410px;
    background: var(--white);
    border-radius: 18px;
    box-shadow: 0 2px 0 var(--grey), 0 14px 30px rgba(0,0,0,0.12);
  }
  .card--front { top: 48px; }
  .card--back  { top: 502px; }

  /* front */
  .brand {
    position: absolute; left: 150px; top: 120px;
    display: flex; align-items: center; gap: 16px;
  }
  .brand__dot {
    width: 30px; height: 30px; border-radius: 50%;
    background: var(--green); flex: none;
  }
  .brand__name {
    font-size: 38px; font-weight: 600; color: var(--ink);
    line-height: 1.15; letter-spacing: -0.3px;
  }
  .abn {
    position: absolute; left: 196px; top: 250px;
    font-size: 20px; font-weight: 400; color: var(--black);
    letter-spacing: 0.3px;
  }

  /* back */
  .contact {
    position: absolute; left: 44px; bottom: 34px;
  }
  .contact__name {
    font-size: 30px; font-weight: 600; color: var(--green);
    text-transform: uppercase; letter-spacing: 0.5px; line-height: 1.1;
  }
  .contact__title {
    font-size: 15px; font-weight: 700; color: var(--black);
    margin-bottom: 10px;
  }
  .contact__list { list-style: none; }
  .contact__row {
    display: flex; align-items: center; gap: 10px;
    font-size: 17px; line-height: 26px; color: var(--black);
  }
  .contact__icon { width: 18px; height: 18px; flex: none; fill: var(--green); }
  .contact__address {
    font-size: 17px; line-height: 22px; color: var(--black);
    margin-top: 4px; font-style: normal;
  }
</style>
</head>
<body>
<main class="sheet">

  <section class="card card--front" aria-label="Card front">
    <div class="brand">
      <span class="brand__dot"></span>
      <span class="brand__name">Veltro<br>Business Solutions</span>
    </div>
    <p class="abn">ABN: 41 208553 917</p>
  </section>

  <section class="card card--back" aria-label="Card back">
    <div class="contact">
      <h1 class="contact__name">Marcus Hale</h1>
      <p class="contact__title">Managing Director</p>
      <ul class="contact__list">
        <li class="contact__row">
          <svg class="contact__icon" viewBox="0 0 18 18" aria-hidden="true"><circle cx="9" cy="5" r="4"/><path d="M1 18c0-5 3.5-8 8-8s8 3 8 8z"/></svg>
          +61 2 5550 1842
        </li>
        <li class="contact__row">
          <svg class="contact__icon" viewBox="0 0 18 18" aria-hidden="true"><rect x="4" y="1" width="10" height="5"/><rect x="1" y="7" width="16" height="7" rx="1"/><rect x="4" y="12" width="10" height="5"/></svg>
          +61 2 55501843
        </li>
        <li class="contact__row">
          <svg class="contact__icon" viewBox="0 0 18 18" aria-hidden="true"><path d="M1 3h16v12H1z M2 4l7 6 7-6" stroke="#fff" stroke-width="1.2"/></svg>
          sales@veltrobiz.com
        </li>
        <li class="contact__row">
          <svg class="contact__icon" viewBox="0 0 18 18" aria-hidden="true"><circle cx="9" cy="9" r="8"/><path d="M1 9h16M9 1c3 3 3 13 0 16M9 1c-3 3-3 13 0 16" stroke="#fff" stroke-width="1" fill="none"/></svg>
          www.veltrobiz.com
        </li>
      </ul>
      <address class="contact__address">Level 4, 27 Harbour Lane, Northbridge<br>NSW 2063</address>
    </div>
  </section>

</main>
</body>
</html>
```